sydney wedding photography business needs a business card design

we need a business card design for a sydney based wedding photography and videography business. our business name is :golden hour studio and film. our target clients are 24-35 yrs female. our style is candid, organic, natural, dynamic. we are a team of young photographers and videographers, and help brides to create memories that they will cherish for the rest of their lives. the logo will be provided. we want an elegant design that reflects our style, and also want to give a great impression to our clients that we are one of the best studios in sydney and our brand means quality and premium service.

Target Market(s)

bride to be, 24-35 years old, living in sydney and surrunding areas

Industry/Entity Type

Wedding Photography

Contact Information for Business Card

address: 57 tarrant street, glenmore nsw 2047
mobile: 0431872259
phone: (02) 9163 2408
info@tidewillowstudio.net.au
www.tidewillowstudio.net.au
facebook:tidewillowweddings
instagram:tidewillowweddings

Font styles to use
Serif
Sans Serif

Requirements
Nice to have
• maybe add my slogan"memories beyond eternity" if the layout looks good
Should not have
• no black color, not good idea for wedding biz card

```html
<!DOCTYPE html>
<html lang="en">
<head>
<meta charset="utf-8">
<title>Golden Hour Studio and Film — Business Card</title>
<link rel="stylesheet" href="https://fonts.googleapis.com/css2?family=Josefin+Sans:wght@400;600&display=swap">
<style>
  :root {
    --backdrop: #efe9df;
    --card-white: #ffffff;
    --mocha: #5a4330;
    --mocha-deep: #46331f;
    --gold: #c9961c;
    --gold-deep: #a8790f;
    --gold-light: #e8bd48;
    --text: #3a3128;
  }
  * { margin: 0; padding: 0; box-sizing: border-box; }
  html, body { width: 1200px; height: 950px; overflow: hidden; }
  body {
    background: var(--backdrop);
    font-family: "Josefin Sans", Arial, sans-serif;
    position: relative;
  }
  .card {
    position: absolute;
    left: 250px;
    width: 700px;
    height: 400px;
    border-radius: 4px;
    overflow: hidden;
    box-shadow: 0 10px 28px rgba(0,0,0,0.2);
  }
  .card-front { top: 50px; background: var(--card-white); }
  .card-back {
    top: 500px;
    background: linear-gradient(135deg, var(--gold-light), var(--gold) 50%, var(--gold-deep));
  }
  .front-art { position: absolute; inset: 0; }
  .brand-name {
    position: absolute;
    left: 30px;
    top: 235px;
    width: 320px;
    text-align: center;
    white-space: nowrap;
    color: var(--gold-light);
    font-weight: 600;
    font-size: 24px;
    letter-spacing: 0.5px;
  }
  .contact {
    position: absolute;
    right: 36px;
    top: 62px;
    text-align: right;
    color: var(--text);
    font-size: 16px;
    line-height: 1.6;
  }
  .contact-name {
    color: var(--gold);
    font-size: 27px;
    font-weight: 400;
    margin-bottom: 6px;
  }
  .contact-line {
    display: flex;
    justify-content: flex-end;
    align-items: center;
    gap: 10px;
    white-space: nowrap;
  }
  .contact-icon { width: 15px; height: 15px; flex: none; }
  .contact-address { margin-top: 14px; }
</style>
</head>
<body>

<section class="card card-front">
  <svg class="front-art" viewBox="0 0 700 400" width="700" height="400" aria-hidden="true">
    <defs>
      <linearGradient id="mochaFill" x1="0" y1="0" x2="1" y2="1">
        <stop offset="0" stop-color="var(--mocha)"/>
        <stop offset="1" stop-color="var(--mocha-deep)"/>
      </linearGradient>
    </defs>
    <path d="M0 0 H320 C420 30 450 120 410 200 C370 280 320 330 300 400 H0 Z" fill="url(#mochaFill)"/>
    <path d="M300 0 H390 C465 30 475 110 445 165 C440 100 405 40 300 0 Z" fill="var(--gold)"/>
    <path d="M40 400 C150 385 255 345 320 290 C305 330 292 365 287 400 Z" fill="var(--gold)"/>
  </svg>

  <div class="brand-name">golden hour studio and film</div>

  <div class="contact">
    <div class="contact-name">Mara Ellison</div>
    <div class="contact-line">(02) 9163 2408
      <svg class="contact-icon" viewBox="0 0 16 16"><path d="M4 1 L6 5 L4.5 6.5 C5.5 8.5 7.5 10.5 9.5 11.5 L11 10 L15 12 L14 15 C7 15 1 9 1 2 Z" fill="var(--gold)"/></svg>
    </div>
    <div class="contact-line">(04) 3187 2259
      <svg class="contact-icon" viewBox="0 0 16 16"><rect x="4" y="1" width="8" height="14" rx="1.5" fill="var(--gold)"/><rect x="5.5" y="3" width="5" height="8" fill="#fff"/></svg>
    </div>
    <div class="contact-line">info@tidewillowstudio.net.au
      <svg class="contact-icon" viewBox="0 0 16 16"><rect x="1" y="3" width="14" height="10" rx="1" fill="var(--gold)"/><path d="M1.5 3.5 L8 9 L14.5 3.5" stroke="#fff" stroke-width="1.3" fill="none"/></svg>
    </div>
    <div class="contact-line">www.tidewillowstudio.net.au
      <svg class="contact-icon" viewBox="0 0 16 16"><circle cx="8" cy="8" r="7" fill="var(--gold)"/><path d="M1 8 H15 M8 1 C4 5 4 11 8 15 M8 1 C12 5 12 11 8 15" stroke="#fff" stroke-width="1" fill="none"/></svg>
    </div>
    <div class="contact-line">tidewillowweddings
      <svg class="contact-icon" viewBox="0 0 16 16"><rect x="1" y="1" width="14" height="14" rx="3" fill="var(--gold)"/></svg>
    </div>
    <div class="contact-line">tidewillowweddings
      <svg class="contact-icon" viewBox="0 0 16 16"><circle cx="8" cy="8" r="7" fill="var(--gold)"/></svg>
    </div>
    <div class="contact-line contact-address">57 tarrant street, glenmore nsw 2047
      <svg class="contact-icon" viewBox="0 0 16 16"><path d="M8 15 C4 10 3 8 3 6 A5 5 0 0 1 13 6 C13 8 12 10 8 15 Z" fill="var(--gold)"/><circle cx="8" cy="6" r="2" fill="#fff"/></svg>
    </div>
  </div>
</section>

<section class="card card-back" aria-label="Card reverse, gold"></section>

</body>
</html>
```